Commercial Real Estate Corporate Site

Our company sells an ERP software to Commercial Real Estate Companies, this project is part of a marketing and sales relaunch of the company.

See attached for PDF formatted Design brief

The software is a modular system where client’s can adopt one module at a time. Our customers are corporate clients who own between 10M and 10B of real estate properties. The typical customer is from the IT or the Financial arm of the company. Our differentiation in the market is that our system is built on a no-code environment, so making changes for the client is quick. Incumbents in the market have long implementation cycles, and customization is often not possible. Competitors are Quorvel, TKB, PlotNest, Vumora.

We need a design for our site which will be implemented into Brevo Forge. **All designs must be compatible with the newest version of Brevo Forge.**

We have produced the following attached assets to use in the website design.:

1. Logo
2. Brand Guidelines
3. Content for Pages
4. Menu Structures
5. Illustrations (modules)
I can't attach them because the files are too big, so they're in this google drive instead:
https://files.examplestore.net/share/k29Xa7Lq0Pz3Rt8MwB5nYc4Hv1Jd6Fe?mode=view

The mechanic for our sales process is as follows:

1. We find on module from our application that a client is interested in. The illustrations that we’ve attached represent the individual modules (elements) of the software.
1. For instance, one of our current customers has purchased a commissions module from us which helps calculate the commission that brokers receive for buying and selling their properties.
2. We provide immense value through the module, and then keep in sales communication with the client to determine which other modules we can implement for them.
1. For instance, in the example above, the client is so happy with the commissions module that they want to start working with our leasing module as well. In the next business quarter, they also choose to add our financials module to their business systems.

### Logo

Attached

### Brand Guidelines

Attached

We are open to suggestions on the secondary colour palette.

### **Site Copy**

**We require the following pages to be created; For now, we will do one Market Page, one Product Page, and one Platform / Services Page, and we will use those as inspiration to create the other dozen Marketing Pages and 30 or so Product Pages.**

**Homepage**

Attached

**Market Page** - look at the quorvel site under the Office, Industrial, Retail (https://www.quorvel.com/products/quorvel-commercial-suite/)

**Product** - One product provided, but there will be 30 - look at the vumora page

(https://www.vumora.com/products/general-accounting)

**Platform / Services Page** - pages that tell the story of our platform and services, content to be provided - the platform will use our modules as it highlights the story of the configurability and composability of the platform. Instead of the icons that they use, we want to use our modules.

- https://www.pelbrix.com/enterprise-applications-platform
- https://www.pelbrix.com/cloud-architecture

**Team Page** - just add sample content for starters (6 Team Members to start)

**Schedule Demo Page** - the call to action for all pages

(https://go.vumora.com/schedule-demo.html)

### Menu Structure

The menu is provided as an attachment.

### Illustrations Information

A note about the illustrations - we have provided an illustrator file with the modules, and if you’d like you can arrange the in any way that you’d like to. We especially like when the modules are positioned like a periodic table of the elements.

Our existing clients are

- Torvane Coop - https://www.torvanecoop.com/real-estate/
- Dalsworth Realestate https://dalsworth.com

Our competitors are

- Quorvel - www.quorvel.com
- TKB - [www.tkbsoftware.com](https://www.tkbsoftware.com/) (we don’t like how this one looks)
- Vumora - www.vumora.com
- Plotnest - www.plotnest.com

Design inspiration

- https://lark-studio.brevosite.com/velmo
- Corporate
- Established
- Modern

### Stock Images Guidance

- https://www.drafta.net/design/QXR7Lm2TpWz/Hk9vN3c8Yd41-FbqsaZRr/edit?utm_content=QXR7Lm2TpWz&utm_campaign=designshare&utm_medium=link2&utm_source=sharebutton

Target Market(s)

Commercial Real Estate Companies - they typically own a portfolio of 50 - 5000 real estate properties and need a software to manage it all.

Coding

Coded - Design and coding required

Number of Pages Required

5+ page

Font styles to use
Other font styles liked:
• Fonts defined in brand guideline

Requirements
Must have
• Brevo Forge, Use the Elemental Design, Download ai.zip and png.zip Use Brand Guideline,
Nice to have
• Check design breif

```html
<!DOCTYPE html>
<html lang="en">
<head>
<meta charset="utf-8">
<title>Tervalis — Mobile Screens</title>
<link rel="stylesheet" href="https://fonts.googleapis.com/css2?family=Audiowide&family=Exo+2:ital,wght@1,600&family=Montserrat:wght@400;500;600&display=swap">
<style>
  :root {
    --ink: #000000;
    --cream: #f8ede3;
    --red: #a10606;
    --brand-red: #e0161b;
    --white: #ffffff;
    --grey-text: #8d8884;
    --hero-text: #d9d9d9;
    --dark-text: #1a1a1a;
  }
  * { margin: 0; padding: 0; box-sizing: border-box; }
  html, body { width: 1200px; height: 1200px; overflow: hidden; background: var(--white); }
  body { position: relative; font-family: "Montserrat", sans-serif; }

  .screen { position: absolute; top: 0; width: 338px; height: 1200px; background: var(--cream); overflow: hidden; }
  .screen--home { left: 50px; top: 37px; height: 1163px; border-radius: 16px 16px 0 0; }
  .screen--about { left: 430px; }
  .screen--story { left: 810px; }

  .abs { position: absolute; }

  /* Hero */
  .hero { position: absolute; left: 0; top: 0; width: 338px; height: 677px; background: var(--ink); }
  .brand { position: absolute; display: flex; align-items: center; gap: 6px; font-family: "Audiowide", sans-serif; font-size: 19px; letter-spacing: 0.5px; }
  .brand__mark { width: 14px; height: 14px; }
  .brand--red { left: 12px; top: 43px; color: var(--brand-red); }
  .brand--red .brand__mark { background: var(--brand-red); }
  .brand--white { left: 28px; top: 1131px; color: var(--white); }
  .brand--white .brand__mark { background: var(--white); }
  .menu-toggle { position: absolute; left: 305px; top: 46px; width: 21px; height: 14px; }

  .tagline { font-family: "Exo 2", sans-serif; font-style: italic; font-weight: 600; font-size: 14px; line-height: 18px; }
  .hero .tagline { position: absolute; left: 9px; top: 115px; width: 310px; color: var(--white); }
  .hero__title { position: absolute; left: 9px; top: 170px; font-family: "Audiowide", sans-serif; font-weight: 400; font-size: 24px; line-height: 36px; color: var(--white); text-transform: uppercase; }
  .hero__text { position: absolute; left: 9px; top: 442px; width: 318px; font-size: 13px; line-height: 18px; color: var(--hero-text); }

  .button { position: absolute; display: flex; align-items: center; background: var(--red); color: var(--white); font-size: 17px; font-weight: 500; border-radius: 2px; }
  .button--center { justify-content: center; }
  .hero .button { left: 9px; top: 589px; width: 320px; height: 51px; }

  .section-title { font-family: "Audiowide", sans-serif; font-weight: 400; font-size: 24px; line-height: 36px; color: var(--ink); text-transform: uppercase; }
  .market__title { position: absolute; left: 0; width: 338px; top: 768px; text-align: center; }
  .market__sub { position: absolute; left: 0; width: 338px; top: 822px; text-align: center; font-size: 13px; color: var(--grey-text); }
  .market__icon { position: absolute; left: 66px; top: 932px; width: 206px; height: 206px; }

  /* About screen */
  .photo { position: absolute; }
  .photo--building { left: 8px; top: 24px; width: 321px; height: 458px; background: linear-gradient(180deg, #a9cdd9 0%, #dfe6e6 35%, #eeeeea 70%, #8f9a6a 100%); }
  .photo-band { position: absolute; background: var(--cream); }
  .about .tagline { position: absolute; left: 8px; top: 527px; width: 310px; color: var(--ink); }
  .about__title { position: absolute; left: 8px; top: 582px; }
  .about__text { position: absolute; left: 8px; top: 672px; width: 322px; font-size: 13px; line-height: 18px; color: var(--grey-text); }
  .about__label { position: absolute; left: 8px; top: 872px; font-size: 14px; font-weight: 600; color: var(--dark-text); }
  .perks { position: absolute; left: 8px; top: 908px; width: 322px; list-style: none; }
  .perk { display: flex; gap: 10px; font-size: 13.5px; line-height: 18px; font-weight: 500; color: var(--dark-text); margin-bottom: 20px; }
  .perk svg { flex: none; width: 16px; height: 16px; margin-top: 10px; }
  .perk--single svg { margin-top: 1px; }
  .about .button { left: 8px; top: 1061px; width: 321px; height: 51px; padding-left: 15px; }

  /* Story screen */
  .story__title { position: absolute; left: 0; width: 338px; top: 162px; text-align: center; }
  .story__text { position: absolute; left: 10px; top: 216px; width: 318px; text-align: center; font-size: 13px; line-height: 18px; color: var(--grey-text); }
  .story .button { left: 10px; top: 360px; width: 319px; height: 50px; }
  .photo--arch-left { left: 0; top: 450px; width: 148px; height: 411px; border-radius: 0 26px 26px 0; background: linear-gradient(160deg, #5e9aa9 0%, #6ea4b0 55%, #b6c2c6 80%, #8c999d 100%); }
  .photo--arch-right { left: 189px; top: 450px; width: 149px; height: 411px; border-radius: 26px 0 0 26px; background: linear-gradient(200deg, #9fb0b4 0%, #c9d0cd 40%, #e4e6e1 65%, #aab6b3 100%); }
  .footer { position: absolute; left: 0; top: 1079px; width: 338px; height: 121px; background: var(--ink); }
  .footer__text { position: absolute; left: 28px; top: 102px; width: 150px; font-size: 11px; line-height: 15px; color: #9b9b9b; }
</style>
</head>
<body>

  <!-- Home screen -->
  <section class="screen screen--home">
    <div class="hero">
      <div class="brand brand--red"><span class="brand__mark"></span>TERVALIS</div>
      <svg class="menu-toggle" viewBox="0 0 21 14" aria-label="Menu">
        <rect x="0" y="0" width="21" height="2" fill="#ffffff"/>
        <rect x="0" y="6" width="21" height="2" fill="#ffffff"/>
        <rect x="0" y="12" width="21" height="2" fill="#ffffff"/>
      </svg>
      <p class="tagline">Unlimited Innovation, Uncompromising Solutions</p>
      <h1 class="hero__title">Welcome to<br>Tervalis — an<br>endless enterprise<br>application<br>platform for the<br>real estate<br>industry.</h1>
      <p class="hero__text">Here, we change the way you look at real estate ERP software. Tervalis is not just another solution — we offer a complete platform that is designed modularly, allowing you to build unlimited combinations of processes and workflows.</p>
      <a class="button button--center">Read More</a>
    </div>
    <h2 class="section-title market__title">Choose your market</h2>
    <p class="market__sub">Find products to drive your business.</p>
    <svg class="market__icon" viewBox="0 0 206 206" aria-label="Commercial building">
      <path d="M90 7 h100 a6 6 0 0 1 6 6 v193 H0 V90 a6 6 0 0 1 6 -6 h84 Z" fill="none" stroke="#000" stroke-width="14" stroke-linejoin="round"/>
      <path d="M44 206 V133 a6 6 0 0 1 6 -6 h38 a6 6 0 0 1 6 6 V206" fill="none" stroke="#000" stroke-width="14"/>
      <rect x="117" y="43" width="14" height="14" fill="#000"/>
      <rect x="161" y="43" width="14" height="14" fill="#000"/>
      <rect x="117" y="87" width="14" height="14" fill="#000"/>
      <rect x="161" y="87" width="14" height="14" fill="#000"/>
      <rect x="117" y="131" width="14" height="14" fill="#000"/>
      <rect x="161" y="131" width="14" height="14" fill="#000"/>
    </svg>
  </section>

  <!-- About screen -->
  <section class="screen screen--about about">
    <div class="photo photo--building" role="img" aria-label="Photo of a white modern apartment building with balconies against a blue sky"></div>
    <div class="photo-band" style="left:166px;top:83px;width:163px;height:12px;"></div>
    <div class="photo-band" style="left:8px;top:267px;width:76px;height:12px;"></div>
    <div class="photo-band" style="left:224px;top:411px;width:105px;height:12px;"></div>
    <p class="tagline">Unlimited Innovation, Uncompromising Solutions</p>
    <h2 class="section-title about__title">About Tervalis<br>Enterprise</h2>
    <p class="about__text">Tervalis is the result of decades of real estate enterprise software development and implementation. Unlike traditional ERP solutions, Tervalis offers a completely new approach. No more need for annoying expensive implementations. No more waiting for updates and upgrades that never come. We start with one module, and from there, you can build with additional modules as your needs dictate.</p>
    <p class="about__label">superiority</p>
    <ul class="perks">
      <li class="perk"><svg viewBox="0 0 16 16"><circle cx="8" cy="8" r="7" fill="#1a1a1a"/><path d="M4.5 8.2 L7 10.6 L11.5 5.6" fill="none" stroke="#f8ede3" stroke-width="1.8"/></svg><span>Bundles Software and Services in a simple annual subscription.</span></li>
      <li class="perk perk--single"><svg viewBox="0 0 16 16"><circle cx="8" cy="8" r="7" fill="#1a1a1a"/><path d="M4.5 8.2 L7 10.6 L11.5 5.6" fill="none" stroke="#f8ede3" stroke-width="1.8"/></svg><span>Modular, Scalable and Secure.</span></li>
      <li class="perk"><svg viewBox="0 0 16 16"><circle cx="8" cy="8" r="7" fill="#1a1a1a"/><path d="M4.5 8.2 L7 10.6 L11.5 5.6" fill="none" stroke="#f8ede3" stroke-width="1.8"/></svg><span>Offers unprecedented flexibility in real estate ERP.</span></li>
    </ul>
    <a class="button">Explore Our Solutions</a>
  </section>

  <!-- Story screen -->
  <section class="screen screen--story story">
    <h2 class="section-title story__title">About us</h2>
    <p class="story__text">Tervalis is a modern alternative to clunky and outdated real estate ERP systems. With decades of experience in global real estate enterprise software development and implementation, we have proven our excellence in providing solutions that suit the needs of modern businesses.</p>
    <a class="button button--center">Explore Our Stories</a>
    <div class="photo photo--arch-left" role="img" aria-label="Photo of a curved white facade under a teal sky"></div>
    <div class="photo photo--arch-right" role="img" aria-label="Photo of layered curved white architecture"></div>
    <footer class="footer">
      <div class="brand brand--white" style="top:52px;"><span class="brand__mark"></span>TERVALIS</div>
      <p class="footer__text">Tervalis is the real estate industry's modern platform</p>
    </footer>
  </section>

</body>
</html>
```